Business Card design project for new family-run construction business

We need a logo and business card designed for a new construction company. We want to convey a professional, but approachable image. We hope to be servicing small residential clients as well as large commercial contracts as well.
Our business will employ a single "Hydro excavator" truck, which can be used for multiple purposes: vacuuming up dirt or water, digging holes, clearing sewer blockages and so on.
We are open to different colour schemes, however blue and white, or yellow/green would be good combinations. We are open to multiple colours (2-4), so long as they are complimentary.

EDIT: Let's not put much emphasis on the octopus... unless it's very clear that the arms are actual vacuum hoses, it won't make sense. An octopus on it's own has little to do with our business.

Please also do not use actual photos of hydro-vac trucks. This is not the aesthetic we are going for.

**The logo should instead be: A stylized outline of a hydrovac truck (a line drawing or digital version of a line-drawing). See the two examples in the attached images of hydrovac trucks. I've also included a very crude pen outline as a reference. Please use your artistic discretion and talent (as I clearly have none) to make something that looks much nicer. Thanks for your efforts!**

The front of the card should have the following elements:
Logo
Name: R & T Hydro Excavation and Flushign
Two phone numbers: Direct and Office
Email address
Website
It should also have the name of the employee and their job title
At the bottom of the card it should say (in a noticeable way): "24/7 Emergency Calls Welcome"

The back of the card should have the following elements:
"20 Years Experience"
"A Canadian Family Run Business"
A small maple-leaf logo that is in a similar style to the rest of the card/logos in the bottom right corner of the back of the card. (see attached)

**We have just added a number of business card designs that really appeal to us to offer inspiration.**

Reason: We have not received designs that hit the mark of what we are looking for. Feedback has been posted, so we would like to provide the designers more time.

Target Market(s)

Commercial and residential customers. As big as large malls and office buildings, as small single-family home owners

Industry/Entity Type

Construction Company

Contact Information for Business Card

We have just added a number of business card designs that really appeal to us to offer inspiration.

Logo
Email address
Website

"20 Years Experience"

Logo Text

R & T Hydro Excavation and Flushing

Font styles to use
Serif
Sans Serif
Other font styles liked:
• Helvetica, Futura, Impact, bold strong, modern fonts that convey a sense of design and style

Colors
0592cd
ec1f27
9bcb3c

Requirements
Must have
• The front of the card should have the following elements:
• Logo
• Name: R & T Hydro Excavation and Flushign
• Two phone numbers: Direct and Office
• Email address
• Website
• It should also have the name of the employee and their job title
• At the bottom of the card it should say (in a noticeable way): "24/7 Emergency Calls Welcome"
• The back of the card should have the following elements:
• "20 Years Experience"
• "A Canadian Family Run Business"
• A small maple-leaf logo that is in a similar style to the rest of the card/logos in the bottom right corner of the back of the card. (see attached)
Nice to have
• The card does not have to be a perfect rectangle. We are open to rounded corners or cut out elements.
• Also embossing, engraving, adding highlighted/glossy layers (spot glass?), or any other effect that will give the card a unique look/feel is more than welcome.
• We would love to have a card that stands out from others and is compelling to look at it, so we are happy to incorporate any sort of modern printing technology to bring out the design.
• Please feel encouraged to be creative and design something unique, especially for this industry.
• Our dream would be if a Scandinavian architect were to go into the construction business and design this business card ;)
Should not have
• Photographs

```html
<!DOCTYPE html>
<html lang="en">
<head>
<meta charset="utf-8">
<title>R &amp; T Hydro Excavation and Flushign — Business Card</title>
<link rel="stylesheet" href="https://fonts.googleapis.com/css2?family=Exo+2:ital,wght@0,400;1,300;1,400&display=swap">
<style>
  :root {
    --ink: #000000;
    --paper: #ffffff;
    --accent: #2ea6df;
    --headline: #2a9fd6;
    --pattern: #1c1c1c;
    --frame: #c8c8c8;
  }
  html, body {
    margin: 0;
    padding: 0;
    width: 1015px;
    height: 1200px;
    overflow: hidden;
    background: var(--paper);
  }
  .card-sheet { display: block; width: 1015px; height: 1200px; }
  .type { font-family: "Exo 2", "Trebuchet MS", sans-serif; }
  .type-italic { font-style: italic; font-weight: 300; }
  .back-headline { fill: var(--headline); font-size: 42px; }
  .brand-name { font-style: normal; font-weight: 400; font-size: 20px; }
  .brand-name--light { fill: var(--paper); }
  .brand-name--dark { fill: var(--ink); font-size: 25px; }
  .contact-line { fill: var(--ink); font-size: 27px; }
  .contact-line--web { font-size: 24px; }
  .person-name { fill: var(--paper); font-size: 46px; }
  .person-role { fill: var(--paper); font-size: 26px; }
  .emergency-line { fill: var(--paper); font-size: 28px; }
</style>
</head>
<body>
<svg class="card-sheet" viewBox="0 0 1015 1200" xmlns="http://www.w3.org/2000/svg">

  <!-- Back of card -->
  <g class="card-back">
    <polygon class="back-panel" points="0,360 344,0 1003,0 1003,574 0,574" fill="var(--ink)"/>
    <polygon class="back-pattern" role="img" aria-label="Faint repeating decorative pattern across the dark panel"
             points="0,360 344,0 1003,0 1003,574 0,574" fill="var(--pattern)" opacity="0.35"/>
    <text class="type type-italic back-headline" x="571" y="250" text-anchor="middle">20 Years Experience</text>
    <text class="type type-italic back-headline" x="571" y="299" text-anchor="middle">A Canadian Family Run Business</text>

    <g class="back-brand">
      <circle cx="690" cy="496" r="34" fill="var(--paper)"/>
      <text class="type brand-name brand-name--light" x="949" y="504" text-anchor="end">R &amp; T Hydro Excavation</text>
      <text class="type brand-name brand-name--light" x="949" y="526" text-anchor="end">and Flushign</text>
    </g>
  </g>

  <!-- Front of card -->
  <g class="card-front">
    <rect class="front-frame" x="13.5" y="625.5" width="1000" height="572" fill="var(--paper)" stroke="var(--frame)" stroke-width="1"/>

    <g class="front-brand">
      <circle cx="250" cy="728" r="50" fill="var(--ink)"/>
      <text class="type brand-name brand-name--dark" x="571" y="772" text-anchor="end">R &amp; T Hydro Excavation</text>
      <text class="type brand-name brand-name--dark" x="571" y="798" text-anchor="end">and Flushign</text>
      <rect class="brand-rule" x="162" y="819" width="419" height="3" fill="var(--accent)"/>
    </g>

    <g class="contact-tabs" fill="var(--accent)">
      <polygon points="442,946 466,924 561,924 533,1003 442,1003"/>
      <polygon points="418,1027 442,1006 528,1006 499,1082 418,1082"/>
      <polygon points="395,1108 418,1085 496,1085 471,1160 395,1160"/>
    </g>

    <polygon class="front-panel" points="670,626 1014,986 1014,1198 457,1198" fill="var(--ink)"/>

    <g class="contact-icons">
      <g class="icon-phone">
        <circle cx="493" cy="963" r="19" fill="var(--paper)"/>
        <path d="M485,953 l5,-2 l4,7 l-3,3 q2,5 7,7 l3,-3 l7,4 l-2,5 q-10,1 -17,-6 q-7,-7 -4,-15 z" fill="var(--ink)"/>
      </g>
      <g class="icon-pin">
        <path d="M463,1022 a15,15 0 0 1 15,15 q0,10 -15,29 q-15,-19 -15,-29 a15,15 0 0 1 15,-15 z" fill="var(--paper)"/>
        <circle cx="463" cy="1037" r="5" fill="var(--ink)"/>
      </g>
      <g class="icon-mail">
        <rect x="418" y="1109" width="48" height="32" rx="4" fill="var(--paper)" stroke="var(--ink)" stroke-width="3"/>
        <path d="M420,1112 l22,17 l22,-17" fill="none" stroke="var(--ink)" stroke-width="3"/>
      </g>
    </g>

    <g class="contact-details">
      <text class="type type-italic contact-line" x="431" y="994" text-anchor="end">555 014 2290 / 555 014 2290</text>
      <text class="type type-italic contact-line" x="401" y="1044" text-anchor="end">410 Harbor Lane Westfield,</text>
      <text class="type type-italic contact-line" x="409" y="1078" text-anchor="end">NY 10098</text>
      <text class="type type-italic contact-line contact-line--web" x="384" y="1120" text-anchor="end">info@rtexcavation.ca</text>
      <text class="type type-italic contact-line contact-line--web" x="384" y="1150" text-anchor="end">www.rtexcavation.ca</text>
    </g>

    <g class="person">
      <text class="type type-italic person-name" x="751" y="982" text-anchor="middle">Marco Dellan</text>
      <text class="type type-italic person-role" x="744" y="1020" text-anchor="middle">President</text>
    </g>

    <text class="type type-italic emergency-line" x="744" y="1153" text-anchor="middle">24/7 Emergency Calls Welcome</text>
  </g>
</svg>
</body>
</html>
```